Design and Renovation Company Luxury Business Card

I want to create a luxury business card for a Design and Renovation Firm . We will use our current logo. The company name is 528BUILDA. We do not want anything standard. We need a very unique concept.
Please see uploaded inspiration. I really like the textured paper option. I would like the card to be thick with debossing, and/or embossing options. The logo has orange in it but I would like to see the card with and without the orange. I think the orange may make the company feel less high-end. The goal is to elevate the logo not match its vibe per se of the logo. We want something very unique, not standard at all!
I would like a space for :
Logo,
Name,
Position,
Email,
Office number,
Website Address,
Business Address,
Thank you!
Have fun!
Target Market(s)
Home owners Age 35 +
Industry/Entity Type
Design and Renovation
Contact Information for Business Card
Logo, Name, Position, Email, Office number, Website Address, Business Address,.
Colors
Designer to choose colors to be used in the design.
Requirements
Must have
- A luxury designer feel. Must be black or dark grey but open to other luxury ideas.
Nice to have
- Gold, silver, black embossing or debossing. Textured paper design.
Should not have
- A cheap look and feel.

```html
<!DOCTYPE html>
<html lang="en">
<head>
<meta charset="utf-8">
<title>528BUILDA Business Card</title>
<link rel="stylesheet" href="https://fonts.googleapis.com/css2?family=Montserrat:wght@400;500;600;700&display=swap">
<style>
  :root {
    --backdrop: #9c9c9c;
    --paper: #f4f4f2;
    --ink: #2a2a2a;
    --card-black: #1c1c1c;
    --accent: #ef9a2e;
    --edge: #d9801c;
    --silver: #ececec;
  }
  * { box-sizing: border-box; margin: 0; padding: 0; }
  html, body {
    width: 1200px; height: 956px; overflow: hidden;
    background: var(--backdrop);
    font-family: "Montserrat", sans-serif;
  }
  .canvas { position: relative; width: 1200px; height: 956px; }

  .card {
    position: absolute;
    width: 580px; height: 332px;
    border-bottom: 4px solid var(--edge);
    box-shadow: 0 18px 40px rgba(0,0,0,0.28);
  }

  /* Front */
  .card-front { left: 110px; top: 130px; background: var(--paper); }
  .holder-name {
    position: absolute; left: 48px; top: 46px;
    color: var(--accent); font-weight: 700; font-size: 30px; letter-spacing: 1px;
  }
  .holder-role {
    position: absolute; left: 48px; top: 84px;
    color: var(--ink); font-size: 13px; font-weight: 500;
  }
  .rule { position: absolute; left: 48px; height: 1.5px; background: var(--accent); }
  .rule-top { top: 116px; width: 300px; }
  .rule-bottom { top: 192px; width: 300px; }
  .address {
    position: absolute; left: 48px; top: 132px;
    color: var(--ink); font-size: 14px; line-height: 20px; font-weight: 500;
  }
  .contacts { position: absolute; left: 48px; top: 210px; list-style: none; }
  .contacts li {
    display: flex; align-items: center; gap: 10px;
    color: var(--ink); font-size: 14px; font-weight: 500; height: 24px;
  }
  .contacts svg { width: 14px; height: 14px; flex: none; }
  .accent-square {
    position: absolute; right: 60px; top: 120px;
    width: 140px; height: 140px; background: var(--accent);
  }

  /* Back */
  .card-back { left: 510px; top: 500px; background: var(--card-black); }
  .brand {
    position: absolute; left: 0; right: 0; top: 110px;
    display: flex; align-items: center; justify-content: center; gap: 18px;
  }
  .brand-square { width: 40px; height: 40px; background: var(--accent); }
  .brand-name {
    color: var(--silver); font-weight: 500; font-size: 56px; letter-spacing: 3px; line-height: 1;
  }
  .brand-tagline {
    position: absolute; left: 0; right: 0; top: 186px; text-align: center;
    color: var(--silver); font-weight: 500; font-size: 15px; letter-spacing: 6px;
  }
</style>
</head>
<body>
<main class="canvas">
  <section class="card card-front">
    <h1 class="holder-name">DANIEL HARTE</h1>
    <p class="holder-role">Medical Director</p>
    <div class="rule rule-top"></div>
    <p class="address">418 Cedar Hollow Lane Suite<br>12 Brookfield, Ohio 44403</p>
    <div class="rule rule-bottom"></div>
    <ul class="contacts">
      <li>
        <svg viewBox="0 0 16 16" aria-hidden="true"><path fill="#ef9a2e" d="M3.5 1.5l2.5 0 1 3.5-1.6 1.2a8 8 0 0 0 4.4 4.4l1.2-1.6 3.5 1v2.5c0 .8-.7 1.5-1.5 1.5A12.5 12.5 0 0 1 2 3c0-.8.7-1.5 1.5-1.5z"/></svg>
        (000)555-0148
      </li>
      <li>
        <svg viewBox="0 0 16 16" aria-hidden="true"><rect x="1" y="3" width="14" height="10" rx="1" fill="#ef9a2e"/><path d="M1.5 4l6.5 5 6.5-5" stroke="#f4f4f2" stroke-width="1.3" fill="none"/></svg>
        hello@528builda.com
      </li>
      <li>
        <svg viewBox="0 0 16 16" aria-hidden="true"><circle cx="8" cy="8" r="7" fill="#ef9a2e"/><path d="M1 8h14M8 1c-3 3.5-3 10.5 0 14M8 1c3 3.5 3 10.5 0 14" stroke="#f4f4f2" stroke-width="1" fill="none"/></svg>
        www.528builda.com
      </li>
    </ul>
    <div class="accent-square"></div>
  </section>

  <section class="card card-back">
    <div class="brand">
      <div class="brand-square"></div>
      <span class="brand-name">528BUILDA</span>
    </div>
    <p class="brand-tagline">Design and Renovation Firm</p>
  </section>
</main>
</body>
</html>
```